Varentoria Business Card and Letter Head

We are a leadership assessment consultancy based in Sydney, Australia. We help executive-level decison-makers select leaders for more senior level roles in corporate and government organisations. Our methodology is based on the latest research from the field of neuroscience.
We need a business card design and matching letter head that presents our company, Varentoria, as a:
1. trusted adviser to senior executive-level decison makers
2. niche consultancy who are experts in the field of assessing leadership talent
3. results-focused solution provider who balance scientific methods with pragmatic solutions
The following company details should be used in all designs:
Company Name: Varentoria
Details (for business card):
Derek Hanford
Prime Capacity Officer
Level 29, Marlow Tower
7 Marlow Square
Sydney, NSW 2000 Australia
Phone: 1300 582 714
Mobile: 0412 637 258
Email: derek.hanford@varentoria-example.com.au
Website: varentoria-example.com.au
I have attached the logo for Varentoria (for both a white and black background) - your business card and letter head designs must incoporate this logo and colour scheme.
Thanks for your interest in this project, I'm looking forward to receiving your ideas.
Regards,
Derek
Target Market(s)
Executive-level decison-makers in corporate and government organisations (e.g., CEO, VP, Head of Human Resources)
Industry/Entity Type
Leadership
Look and feel

```html
<!DOCTYPE html>
<html lang="en">
<head>
<meta charset="utf-8">
<title>Varentoria Business Card</title>
<link rel="stylesheet" href="https://fonts.googleapis.com/css2?family=Open+Sans:wght@400;600;700&display=swap">
<style>
  :root {
    --brand-red: #c22a1f;
    --brand-dark: #3c3c3e;
    --brand-grey: #e4e4e4;
    --paper: #ffffff;
    --backdrop: #ecebe8;
  }
  * { margin: 0; padding: 0; box-sizing: border-box; }
  html, body { width: 1200px; height: 1094px; overflow: hidden; }
  body {
    background: var(--backdrop);
    font-family: "Open Sans", sans-serif;
    position: relative;
  }
  .card {
    position: absolute;
    left: 190px;
    width: 820px;
    height: 500px;
    background: var(--paper);
    border-radius: 40px;
    overflow: hidden;
    box-shadow: 0 6px 18px rgba(0,0,0,0.18);
  }
  .card--front { top: 32px; }
  .card--back { top: 562px; }
  .card__waves { position: absolute; inset: 0; width: 100%; height: 100%; }
  .brand {
    position: absolute;
    display: flex;
    align-items: center;
    gap: 16px;
    color: var(--brand-dark);
    font-weight: 600;
  }
  .brand__mark { background: var(--brand-dark); }
  .card--front .brand { left: 60px; top: 52px; font-size: 52px; }
  .card--front .brand__mark { width: 44px; height: 44px; }
  .card--back .brand { left: 150px; top: 110px; font-size: 84px; }
  .card--back .brand__mark { width: 70px; height: 70px; }
  .faint-square {
    position: absolute;
    left: 630px; top: 34px;
    width: 100px; height: 100px;
    background: var(--brand-grey);
    opacity: 0.6;
  }
  .address {
    position: absolute;
    left: 60px; top: 200px;
    color: var(--brand-red);
    font-size: 17px;
    line-height: 1.5;
  }
  .contact {
    position: absolute;
    right: 42px;
    color: var(--paper);
    font-size: 17px;
    line-height: 1.6;
    text-align: right;
  }
  .contact--phones { top: 262px; }
  .contact--online { top: 360px; }
  .contact__line { display: flex; align-items: center; justify-content: flex-end; gap: 10px; }
  .contact__icon { width: 15px; height: 15px; flex: none; fill: var(--paper); }
  .person {
    position: absolute;
    left: 60px; top: 410px;
    color: var(--paper);
  }
  .person__name { font-size: 23px; font-weight: 700; }
  .person__title { font-size: 16px; }
  .website {
    position: absolute;
    left: 0; right: 0; top: 420px;
    text-align: center;
    color: var(--paper);
    font-size: 30px;
    letter-spacing: 4px;
  }
</style>
</head>
<body>

<section class="card card--front">
  <svg class="card__waves" viewBox="0 0 820 500" preserveAspectRatio="none" aria-hidden="true">
    <path d="M0,278 C120,358 220,388 330,348 S600,198 820,118 L820,500 L0,500 Z" fill="var(--brand-dark)"/>
    <path d="M0,290 C120,370 220,400 330,360 S600,210 820,130" fill="none" stroke="var(--paper)" stroke-width="4"/>
    <path d="M0,300 C120,380 220,410 330,370 S600,220 820,140 L820,500 L0,500 Z" fill="var(--brand-red)"/>
  </svg>
  <div class="faint-square"></div>
  <div class="brand"><span class="brand__mark"></span>Varentoria</div>
  <div class="address">
    <p>Level 29, Marlow Tower</p>
    <p>7 Marlow Square</p>
    <p>Sydney, NSW 2000 Australia</p>
  </div>
  <div class="contact contact--phones">
    <p class="contact__line">
      <svg class="contact__icon" viewBox="0 0 16 16"><path d="M3.5 1l2.5 3-1.5 2c1 2 2.5 3.5 4.5 4.5l2-1.5 3 2.5-1.5 2.5C7 14 2 9 1 2.5z"/></svg>1300 582 714
    </p>
    <p class="contact__line">
      <svg class="contact__icon" viewBox="0 0 16 16"><path d="M4 0h8v16H4z M5.5 2v10h5V2z" fill-rule="evenodd"/></svg>0412 637 258
    </p>
  </div>
  <div class="contact contact--online">
    <p class="contact__line">
      <svg class="contact__icon" viewBox="0 0 16 16"><path d="M0 3h16v10H0z"/><path d="M1.5 4.5L8 9l6.5-4.5" fill="none" stroke="var(--brand-red)" stroke-width="1.2"/></svg>derek.hanford@varentoria-example.com.au
    </p>
    <p class="contact__line">
      <svg class="contact__icon" viewBox="0 0 16 16"><circle cx="8" cy="8" r="7.5"/></svg>www.varentoria-example.com.au
    </p>
  </div>
  <div class="person">
    <p class="person__name">Derek Hanford</p>
    <p class="person__title">Prime Capacity Officer</p>
  </div>
</section>

<section class="card card--back">
  <svg class="card__waves" viewBox="0 0 820 500" preserveAspectRatio="none" aria-hidden="true">
    <path d="M0,260 C160,320 300,390 480,372 S700,335 820,355 L820,500 L0,500 Z" fill="var(--brand-dark)"/>
    <path d="M0,272 C160,332 300,402 480,384 S700,347 820,367" fill="none" stroke="var(--paper)" stroke-width="4"/>
    <path d="M0,282 C160,342 300,412 480,394 S700,357 820,377 L820,500 L0,500 Z" fill="var(--brand-red)"/>
  </svg>
  <div class="brand"><span class="brand__mark"></span>Varentoria</div>
  <p class="website">www.varentoria-example.com.au</p>
</section>

</body>
</html>
```